Local fast-growing company in the service sector

We are looking for a modern business card design, which should also appear on our letterheads

Target Market(s)

Private and industrial sectors

Contact Information for Business Card

Vorname Name
Kellberger Str. 18
72418 Lindenhausen
Tel.: 07146-839214-0
Name@agentur-kvtl.de

Colors
9d9d9d
919191
aaaaaa

Requirements
Must have
• The logo (file) in silver

```html
<!DOCTYPE html>
<html lang="de">
<head>
<meta charset="utf-8">
<title>KVTL – Visitenkarte</title>
<link rel="stylesheet" href="https://fonts.googleapis.com/css2?family=Michroma&family=Questrial&display=swap">
<style>
  :root {
    --page-bg: #dedede;
    --card-centre: #3b3b3b;
    --card-edge: #1f1f1f;
    --silver: #aaaaaa;
    --silver-light: #d4d4d4;
    --text-light: #e6e6e6;
  }
  * { margin: 0; padding: 0; box-sizing: border-box; }
  html, body {
    width: 1200px;
    height: 576px;
    overflow: hidden;
    background: var(--page-bg);
  }
  .sheet { position: relative; width: 1200px; height: 576px; }
  .card {
    position: absolute;
    border-radius: 11px;
    background: radial-gradient(ellipse at 50% 42%, var(--card-centre) 0%, #2a2a2a 55%, var(--card-edge) 100%);
    overflow: hidden;
  }
  .card--front { left: 82px; top: 139px; width: 485px; height: 293px; }
  .card--back  { left: 602px; top: 138px; width: 481px; height: 291px; }

  .brand {
    position: absolute;
    display: flex;
    align-items: center;
    color: var(--silver-light);
    font-family: "Michroma", sans-serif;
  }
  .brand__square { background: var(--silver); flex: none; }
  .brand__words { display: flex; flex-direction: column; }
  .brand__name { line-height: 1; letter-spacing: 0.02em; white-space: nowrap; }
  .brand__web {
    font-family: "Questrial", sans-serif;
    color: var(--silver-light);
    letter-spacing: 0.08em;
    white-space: nowrap;
  }

  .card--front .brand { left: 87px; top: 95px; gap: 21px; }
  .card--front .brand__square { width: 94px; height: 94px; }
  .card--front .brand__name { font-size: 54px; }
  .card--front .brand__web { font-size: 17px; margin-top: 8px; }

  .card--back .brand { left: 44px; top: 42px; gap: 20px; }
  .card--back .brand__square { width: 62px; height: 62px; }
  .card--back .brand__name { font-size: 38px; }
  .card--back .brand__web { font-size: 13px; margin-top: 5px; }

  .contact {
    position: absolute;
    left: 227px;
    top: 174px;
    color: var(--text-light);
    font-family: "Questrial", sans-serif;
    font-style: normal;
  }
  .contact__name {
    font-family: "Michroma", sans-serif;
    font-size: 15px;
    line-height: 18px;
    letter-spacing: 0.03em;
    margin-left: -4px;
    margin-bottom: 10px;
    white-space: nowrap;
  }
  .contact__line {
    display: flex;
    align-items: center;
    gap: 13px;
    font-size: 13px;
    line-height: 17px;
    height: 17px;
    letter-spacing: 0.03em;
    white-space: nowrap;
  }
  .contact__line svg { width: 10px; height: 10px; fill: var(--text-light); flex: none; }
  .contact__address {
    font-size: 13.5px;
    line-height: 18px;
    letter-spacing: 0.03em;
    margin-top: 2px;
    white-space: nowrap;
  }
</style>
</head>
<body>
<main class="sheet">
  <section class="card card--front" aria-label="Vorderseite">
    <div class="brand">
      <span class="brand__square"></span>
      <div class="brand__words">
        <span class="brand__name">KVTL</span>
        <span class="brand__web">agentur-kvtl.de</span>
      </div>
    </div>
  </section>

  <section class="card card--back" aria-label="Rückseite">
    <div class="brand">
      <span class="brand__square"></span>
      <div class="brand__words">
        <span class="brand__name">KVTL</span>
        <span class="brand__web">agentur-kvtl.de</span>
      </div>
    </div>

    <address class="contact">
      <p class="contact__name">VORNAME NAME</p>
      <p class="contact__line">
        <svg viewBox="0 0 10 10" aria-hidden="true"><path d="M1 3.5C1 2 2.5 1.5 5 1.5S9 2 9 3.5L7.5 4 7 3H3L2.5 4zM2.5 5h5l1 3.5h-7z"/></svg>
        07146-839214-0
      </p>
      <p class="contact__line">
        <svg viewBox="0 0 10 10" aria-hidden="true"><path d="M0.5 2h9v6h-9zM1.2 2.6 5 5.6 8.8 2.6v-0.1H1.2z" fill-rule="evenodd"/></svg>
        Name@agentur-kvtl.de
      </p>
      <p class="contact__address">Kellberger Str. 18 72418 Lindenhausen</p>
    </address>
  </section>
</main>
</body>
</html>
```